Salon and Spa Distributor Business Card

Need a business card. We are are distributor in the salon and spa industry. We identify with natural beauty. Need a card with:
Company Name: Petal Quarry"
Title: "President & CEO"
Address
Company Phone number
email
website
Tag Line:" The Natural Beauty Supplier"

Industry/Entity Type

Business

Contact Information for Business Card

Name: Dov Strommen
Title: "President & CEO"
Address: 31 Harlow Ln, Bexmoor, NJ 07813
Company Phone number: 800-463-5918
email: dovstrommen@petalquarry.example
website: www.petalquarry.example

Requirements
Should not have
• No black backgrounds

```html
<!DOCTYPE html>
<html lang="en">
<head>
<meta charset="utf-8">
<title>Petal Quarry – Business Card</title>
<link rel="stylesheet" href="https://fonts.googleapis.com/css2?family=Questrial&display=swap">
<style>
  :root {
    --page-bg: #e9ebe8;
    --green-light: #62bb47;
    --green-mid: #2f9a3e;
    --green-deep: #0b6f32;
    --brand-green: #3aa640;
    --ink: #1c1c1c;
    --muted: #3d3d3d;
    --white: #ffffff;
  }
  * { box-sizing: border-box; margin: 0; padding: 0; }
  html, body { width: 1200px; height: 780px; overflow: hidden; }
  body {
    background: var(--page-bg);
    font-family: "Questrial", "Century Gothic", sans-serif;
    position: relative;
  }
  .card {
    position: absolute;
    top: 235px;
    width: 540px;
    height: 309px;
    overflow: hidden;
    box-shadow: 0 10px 26px rgba(0,0,0,0.18);
  }
  /* Front */
  .card--front {
    left: 40px;
    background: linear-gradient(200deg, var(--green-light) 0%, var(--green-mid) 50%, var(--green-deep) 100%);
    color: var(--white);
  }
  .front-brand {
    position: absolute;
    left: 120px;
    top: 104px;
    display: flex;
    align-items: center;
    gap: 16px;
  }
  .front-brand__dot {
    width: 58px; height: 58px;
    border-radius: 50%;
    background: var(--white);
  }
  .front-brand__name {
    font-size: 40px;
    letter-spacing: 0.5px;
    color: var(--white);
    white-space: nowrap;
  }
  .front-tagline {
    position: absolute;
    left: 120px;
    top: 196px;
    font-size: 15px;
    letter-spacing: 3px;
    color: var(--white);
    white-space: nowrap;
  }
  /* Back */
  .card--back {
    left: 620px;
    background: var(--white);
    color: var(--ink);
  }
  .back-brand {
    position: absolute;
    left: 26px;
    top: 22px;
  }
  .back-brand__name {
    font-size: 34px;
    color: var(--brand-green);
    line-height: 1;
    white-space: nowrap;
  }
  .back-brand__tagline {
    font-size: 12.5px;
    color: var(--muted);
    margin-top: 4px;
    letter-spacing: 0.3px;
    white-space: nowrap;
  }
  .person {
    position: absolute;
    left: 26px;
    top: 104px;
  }
  .person__name { font-size: 19px; color: var(--brand-green); }
  .person__title { font-size: 14px; color: var(--ink); margin-top: 2px; }
  .contact {
    position: absolute;
    left: 26px;
    top: 168px;
    font-size: 14px;
    line-height: 1.45;
    color: var(--ink);
  }
  .contact__address { margin-bottom: 2px; }
  .contact__row { display: flex; align-items: center; gap: 7px; white-space: nowrap; }
  .contact__icon {
    width: 13px; height: 13px;
    background: var(--brand-green);
    border-radius: 2px;
    display: inline-flex;
    align-items: center;
    justify-content: center;
    flex: none;
  }
  .contact__icon svg { width: 9px; height: 9px; }
  .back-artwork {
    position: absolute;
    right: 0;
    top: 70px;
    width: 230px;
    height: 239px;
    background: radial-gradient(closest-side at 55% 55%, var(--green-light) 0%, var(--green-mid) 60%, rgba(255,255,255,0) 100%);
    opacity: 0.9;
  }
</style>
</head>
<body>

  <section class="card card--front" aria-label="Business card front">
    <div class="front-brand">
      <span class="front-brand__dot"></span>
      <span class="front-brand__name">Petal Quarry</span>
    </div>
    <p class="front-tagline">The Natural Beauty Supplier</p>
  </section>

  <section class="card card--back" aria-label="Business card back">
    <div class="back-brand">
      <p class="back-brand__name">Petal Quarry</p>
      <p class="back-brand__tagline">The Natural Beauty Supplier</p>
    </div>

    <div class="person">
      <p class="person__name">Dov Strommen</p>
      <p class="person__title">President &amp; CEO</p>
    </div>

    <div class="contact">
      <p class="contact__address">31 Harlow Ln,<br>Bexmoor, NJ 07813</p>
      <p class="contact__row">
        <span class="contact__icon"><svg viewBox="0 0 10 10"><path d="M2 1h2l1 2-1.2 1a6 6 0 0 0 2.2 2.2L7 5l2 1v2c-4 .5-7.5-3-7-7z" fill="#fff"/></svg></span>
        800-463-5918
      </p>
      <p class="contact__row">
        <span class="contact__icon"><svg viewBox="0 0 10 10"><rect x="1" y="2.5" width="8" height="5" fill="none" stroke="#fff" stroke-width="1"/><path d="M1 2.5l4 3 4-3" fill="none" stroke="#fff" stroke-width="1"/></svg></span>
        dovstrommen@petalquarry.example
      </p>
      <p class="contact__row">
        <span class="contact__icon"><svg viewBox="0 0 10 10"><circle cx="5" cy="5" r="3.8" fill="none" stroke="#fff" stroke-width="1"/><path d="M1.2 5h7.6M5 1.2c-2 2.4-2 5.2 0 7.6M5 1.2c2 2.4 2 5.2 0 7.6" fill="none" stroke="#fff" stroke-width="0.8"/></svg></span>
        www.petalquarry.example
      </p>
    </div>

    <div class="back-artwork" role="img" aria-label="Green brand illustration area with flowing hair and leaves"></div>
  </section>

</body>
</html>
```